Bramblewick Homes Tarrow Customer Brochure

Need a brochure designed that is clean and minimal that contains our logo, and contact information. Would like an area where we could insert business cards, and slips on both sides of the openings to place sheets of paper in. Would prefer to have the COVER LETTER I have attached printed on one side of the opening.

Target Market(s)

Home buyers

Font styles to use
Sans Serif

Colors

Designer to choose colors to be used in the design.

Requirements
Must have
• Logo, contact info, website, etc. Must be minimal in design and very clean looking.
Nice to have
• Please see above
Should not have
• No stock pictures of homes, builds, etc. Need it to look very clean

```html
<!DOCTYPE html>
<html lang="en">
<head>
<meta charset="utf-8">
<title>Bramblewick Homes Tarrow – Presentation Folder</title>
<link rel="stylesheet" href="https://fonts.googleapis.com/css2?family=Lato:ital,wght@0,400;0,700;0,900;1,400;1,700&display=swap">
<style>
  :root {
    --tan: #d2a679;
    --tan-light: #e6c9a8;
    --charcoal: #333132;
    --grey: #8a8a8a;
    --white: #ffffff;
    --backdrop: #e4e4e4;
  }
  * { box-sizing: border-box; margin: 0; padding: 0; }
  html, body { width: 960px; height: 1200px; overflow: hidden; }
  body {
    background: var(--backdrop);
    font-family: "Lato", Arial, sans-serif;
    position: relative;
  }

  /* every panel is built at 440 × 624 and scaled into place */
  .panel {
    position: absolute;
    width: 440px;
    height: 624px;
    overflow: hidden;
    transform: scale(0.682);
    transform-origin: 0 0;
    box-shadow: 0 6px 18px rgba(0,0,0,0.18);
  }
  .panel--letter  { left: 20px;  top: 70px;  background: var(--tan); }
  .panel--pocket  { left: 320px; top: 70px;  background: var(--white); box-shadow: 6px 6px 18px rgba(0,0,0,0.14); }
  .panel--profile { left: 640px; top: 70px;  background: var(--white); }
  .panel--back    { left: 170px; top: 580px; background: var(--tan); }
  .panel--front   { left: 490px; top: 580px; background: var(--white); }
  .panel__shapes { position: absolute; inset: 0; width: 100%; height: 100%; }

  /* brand lockup */
  .brand {
    position: absolute;
    left: 0; right: 0;
    display: flex;
    flex-direction: column;
    align-items: center;
  }
  .brand__square { background: var(--charcoal); }
  .brand__name {
    font-weight: 700;
    color: var(--charcoal);
    text-transform: uppercase;
    text-align: center;
    line-height: 1.15;
  }
  .panel--back .brand { top: 238px; }
  .panel--back .brand__square { width: 62px; height: 62px; margin-bottom: 8px; }
  .panel--back .brand__name { font-size: 14px; letter-spacing: 1px; }

  .panel--front .brand { top: 250px; }
  .panel--front .brand__square { width: 102px; height: 102px; margin-bottom: 12px; }
  .panel--front .brand__name { font-size: 24px; letter-spacing: 2px; }
  .brand__web { margin-top: 12px; font-size: 10px; letter-spacing: 2px; color: var(--charcoal); }
  .brand__rule { width: 104px; height: 2px; margin-top: 6px; background: var(--tan-light); }

  /* contact list on back cover */
  .contact {
    position: absolute;
    top: 365px; left: 0; right: 0;
    list-style: none;
    text-align: center;
    color: var(--white);
    font-size: 10px;
    font-weight: 700;
  }
  .contact__item { margin-bottom: 11px; }
  .contact__icon { display: block; margin: 0 auto 4px; width: 11px; height: 11px; }
  .social {
    position: absolute;
    top: 575px; left: 0; right: 0;
    display: flex; justify-content: center; gap: 16px;
  }
  .social__dot { width: 17px; height: 17px; border-radius: 50%; background: var(--white); }

  /* cover letter */
  .letter {
    position: absolute;
    top: 26px; left: 40px; right: 34px;
    color: var(--white);
    font-size: 10.5px;
    line-height: 1.5;
  }
  .letter__greeting { font-weight: 700; font-style: italic; margin-bottom: 8px; }
  .letter__para { margin-bottom: 8px; }
  .letter__sign { margin-top: 14px; margin-left: 170px; font-style: italic; font-size: 10px; }
  .letter__signer { font-weight: 700; }
  .letter-contact {
    position: absolute;
    top: 330px; left: 200px;
    list-style: none;
    color: var(--white);
    font-size: 8.5px;
  }
  .letter-contact__mark { width: 26px; height: 26px; background: var(--charcoal); margin: 0 0 10px 8px; }
  .letter-contact__item { display: flex; align-items: center; gap: 6px; margin-bottom: 5px; }
  .dot { width: 6px; height: 6px; border-radius: 50%; background: var(--charcoal); flex: none; }

  /* corporate profile sheet */
  .profile__mark { position: absolute; top: 60px; left: 199px; width: 42px; height: 42px; background: var(--charcoal); }
  .profile__brand { position: absolute; top: 107px; left: 0; right: 0; text-align: center; font-size: 9px; font-weight: 700; letter-spacing: 1px; color: var(--charcoal); text-transform: uppercase; }
  .profile__title { position: absolute; top: 128px; left: 0; right: 0; text-align: center; font-size: 25px; font-weight: 900; color: var(--charcoal); }
  .profile__title span { color: var(--grey); font-weight: 700; }
  .profile__body { position: absolute; top: 172px; left: 44px; right: 44px; font-size: 10px; line-height: 1.55; color: #555; text-align: justify; }
  .profile__contact { position: absolute; top: 300px; left: 44px; list-style: none; font-size: 8.5px; color: #555; }
  .profile__contact li { display: flex; align-items: center; gap: 6px; margin-bottom: 5px; }
</style>
</head>
<body>

  <!-- inside spread: cover letter side -->
  <section class="panel panel--letter" aria-label="Inside left with cover letter">
    <svg class="panel__shapes" viewBox="0 0 440 624" aria-hidden="true">
      <polygon points="0,480 60,440 150,470 150,560 70,600 0,570" fill="#e0bf99"/>
      <polyline points="0,460 90,400 110,470 60,600" fill="none" stroke="#333132" stroke-width="2.5"/>
      <line x1="0" y1="620" x2="440" y2="620" stroke="#c4976a" stroke-width="1"/>
    </svg>
    <div class="letter">
      <p class="letter__greeting">Dear Homeowner,</p>
      <p class="letter__para">Thank you for considering us to build your next home. For many years our family has crafted houses across the region with care, honest pricing and close attention to every detail.</p>
      <p class="letter__para">From the first sketch to the final walkthrough, our team stays beside you, answering questions and keeping your build on schedule and on budget.</p>
      <p class="letter__para">Inside this folder you will find our corporate profile and details on current projects. We look forward to building with you.</p>
      <p class="letter__sign">Yours truly,<br><span class="letter__signer">Martin Ellery</span><br>Founder and President</p>
    </div>
    <ul class="letter-contact">
      <li class="letter-contact__mark"></li>
      <li class="letter-contact__item"><span class="dot"></span>555-014-0123</li>
      <li class="letter-contact__item"><span class="dot"></span>555-014-0155</li>
      <li class="letter-contact__item"><span class="dot"></span>info@bramblewickhomestarrow.com</li>
      <li class="letter-contact__item"><span class="dot"></span>18 millrace rd. tarrow-on-the-lake, ontario, x0x 0x0.</li>
    </ul>
  </section>

  <!-- inside spread: pocket side with card slot and sheet slips -->
  <section class="panel panel--pocket" aria-label="Inside right with pocket and business card slot">
    <svg class="panel__shapes" viewBox="0 0 440 624" aria-hidden="true">
      <path d="M0,624 V420 Q0,340 80,340 H440 V624 Z" fill="#333132"/>
      <polygon points="210,470 300,410 400,470 400,560 300,624 210,560" fill="none" stroke="#9a9a9a" stroke-width="2"/>
      <polygon points="280,520 370,460 440,500 440,624 300,624 280,600" fill="#d2a679"/>
      <!-- business card slot -->
      <line x1="60" y1="400" x2="82" y2="382" stroke="#6b6869" stroke-width="2"/>
      <line x1="170" y1="382" x2="192" y2="400" stroke="#6b6869" stroke-width="2"/>
      <!-- sheet slips -->
      <line x1="12" y1="600" x2="34" y2="622" stroke="#6b6869" stroke-width="2"/>
      <line x1="20" y1="30" x2="44" y2="6" stroke="#d8d8d8" stroke-width="2"/>
      <line x1="396" y1="6" x2="420" y2="30" stroke="#d8d8d8" stroke-width="2"/>
    </svg>
  </section>

  <!-- insert sheet -->
  <section class="panel panel--profile" aria-label="Corporate profile sheet">
    <svg class="panel__shapes" viewBox="0 0 440 624" aria-hidden="true">
      <polygon points="0,470 200,500 290,560 350,624 0,624" fill="#d2a679"/>
      <polyline points="230,624 260,530 380,530 440,590" fill="none" stroke="#333132" stroke-width="2.5"/>
    </svg>
    <div class="profile__mark"></div>
    <div class="profile__brand">Bramblewick Homes</div>
    <h1 class="profile__title">Corporate <span>Profile</span></h1>
    <p class="profile__body">Bramblewick Homes is a family-run builder creating custom homes and quiet communities across the Tarrow region. Every project pairs careful planning with skilled trades and durable materials. We believe a home should feel personal, so each design begins with a conversation about how you live. Our goal is simple: deliver quality that lasts for generations.</p>
    <ul class="profile__contact">
      <li><span class="dot"></span>555-014-0123</li>
      <li><span class="dot"></span>555-014-0155</li>
      <li><span class="dot"></span>info@bramblewickhomestarrow.com</li>
      <li><span class="dot"></span>18 millrace rd. tarrow-on-the-lake, ontario, x0x 0x0.</li>
    </ul>
  </section>

  <!-- back cover -->
  <section class="panel panel--back" aria-label="Back cover">
    <svg class="panel__shapes" viewBox="0 0 440 624" aria-hidden="true">
      <polyline points="0,175 169,69 177,0" fill="none" stroke="#e0bf99" stroke-width="11"/>
      <polyline points="331,0 331,47 440,125" fill="none" stroke="#333132" stroke-width="2.5"/>
    </svg>
    <div class="brand">
      <div class="brand__square"></div>
      <div class="brand__name">Bramblewick<br>Homes</div>
    </div>
    <ul class="contact">
      <li class="contact__item">
        <svg class="contact__icon" viewBox="0 0 12 12"><path d="M3 1 L5 3.5 L4 5 Q5 7 7 8 L8.5 7 L11 9 L10 11 Q5 11 1 6 Q1 2 3 1Z" fill="#333132"/></svg>
        555-014-0123
      </li>
      <li class="contact__item">
        <svg class="contact__icon" viewBox="0 0 12 12"><rect x="3" y="1" width="6" height="3" fill="#333132"/><rect x="1" y="4.5" width="10" height="5" rx="1" fill="#333132"/><rect x="3" y="8" width="6" height="3" fill="#333132"/></svg>
        555-014-0155
      </li>
      <li class="contact__item">
        <svg class="contact__icon" viewBox="0 0 12 12"><circle cx="6" cy="6" r="5" fill="none" stroke="#333132" stroke-width="1.4"/><line x1="1" y1="6" x2="11" y2="6" stroke="#333132" stroke-width="1.2"/><ellipse cx="6" cy="6" rx="2.2" ry="5" fill="none" stroke="#333132" stroke-width="1.2"/></svg>
        www.bramblewickhomestarrow.com
      </li>
      <li class="contact__item">
        <svg class="contact__icon" viewBox="0 0 12 12"><rect x="1" y="2.5" width="10" height="7" fill="#333132"/><polyline points="1,2.5 6,6.5 11,2.5" fill="none" stroke="#d2a679" stroke-width="1"/></svg>
        info@bramblewickhomestarrow.com
      </li>
      <li class="contact__item">
        <svg class="contact__icon" viewBox="0 0 12 12"><path d="M6 11.5 L2.5 6 A4 4 0 1 1 9.5 6 Z" fill="#333132"/><circle cx="6" cy="4.3" r="1.5" fill="#d2a679"/></svg>
        18 millrace rd. tarrow-on-the-lake, ontario, x0x 0x0.
      </li>
    </ul>
    <div class="social" aria-label="Social media">
      <span class="social__dot"></span>
      <span class="social__dot"></span>
    </div>
  </section>

  <!-- front cover -->
  <section class="panel panel--front" aria-label="Front cover">
    <svg class="panel__shapes" viewBox="0 0 440 624" aria-hidden="true">
      <polygon points="56,0 236,0 236,50 145,115 56,50" fill="#d2a679"/>
      <polyline points="0,123 122,37 122,0" fill="none" stroke="#333132" stroke-width="2.5"/>
      <polygon points="156,624 156,544 297,488 440,583 440,624" fill="#d2a679"/>
      <polyline points="278,624 278,566 383,494 440,532" fill="none" stroke="#333132" stroke-width="2.5"/>
    </svg>
    <div class="brand">
      <div class="brand__square"></div>
      <div class="brand__name">Bramblewick<br>Homes</div>
      <div class="brand__web">www.bramblewickhomestarrow.com</div>
      <div class="brand__rule"></div>
    </div>
  </section>

</body>
</html>
```